Flyer-Design für Kanutouristiker (Kanu Vermietung) Folgeaufträge!!
Zielgruppe
Wir veranstalten Kanu - und Erlebnistouren. Vermieten Kanus, Schlauchboote (Rafts), SUP (Stand up Paddling) und Fahrräder.
Für Gruppen, Betriebe, Schulklassen, Vereine, Familien, Junggesellenabschiede, Geburtstage usw.
Aufgabenstellung
Wir möchten einen ansprechenden Flyer erstellen lassen, der Lust auf unsere Angebote machen soll.
Hier handelt es sich um einen DIN lang (A4) Wickelfalz Falter (6 Seiter)
Mit unseren Angeboten. Beispielbilder sind im Anhang mithochgeladen. Es können weitere geliefert werden- oder Sie sehen sich einmal auf unserer Webseite um.
Wenig Text- lassen Sie die Bilder sprechen!!
Der Flyer soll lust auf eine Tour bei uns machen!
Der Flyer soll natürlich wirken.
Unsere CI wird schon durch unser Logo mitgegeben- es müssen nicht unbeding gr. Flächen mit unseren Farben gefüllt werden!!
Uns sprechen filigrane, künstlerische Designs an. Aber bitte die natürlichkeit nicht aus den Augen verlieren. Wir sind OUTDOORveranstalter- unsere Aktionen finden in der Natur statt!
Eine Variante, die ich aus zahlreichen Designs erarbeitet habe:
Nutzen Sie ein grosses Bild als Header (Kopfzeile) das auch z.B. im Orangeton (Logofarbe) überzeichnet - oder auch nur weiss (milchig) verändert sein darf.
Hierauf einen geeigneten Sinnspruch (Überschrift) z.B. "..mehr als nur ein Abenteuer"
der passend sein muss.
Etwas Poetisches vielleicht.... kurz und prägnant. (Natur, ökologie, Wasser, reisen...).
Bilder groß und darauf überlagert kleinere eingefasst in Rahmen.
Zum Textinhalt
Titelseite:
was machen wir?
Paddel- & Radtouren im Weser-Leinebergland, tolles Bild und unser Logo
evtl. noch für wen geeignet?
Schulklassen, Betriebe, Vereine, Familien, Junggesellenabschiede etc.
Innenseite(n):
Bilder, Bilder, Bilder (vielleicht gr. Hintergrundbild, dann kleine Bilder drauf mit passender Überschrift: z.B. Abenteuer im Flinkfloss, Stand up paddling, Teambuilding Flossbau, Radverleih, Paddel & Pedale, usw.
Rückseite:
Unsere Kontaktdaten
Firmenname
Webseite
Mailadresse
Hausanschrift
facebook
QR Code
LOGO
Toll wäre ein..

```html
<!DOCTYPE html>
<html lang="de">
<head>
<meta charset="utf-8">
<title>Flusszeit – Flyer Wickelfalz</title>
<link href="https://fonts.googleapis.com/css2?family=Cabin:wght@400;500;600;700&display=swap" rel="stylesheet">
<style>
  :root{
    --stage:#5f7384;
    --orange:#e3891d;
    --orange-panel:#e49a2c;
    --red:#8f1c15;
    --red-tag:#c4241b;
    --blue:#2b6a8c;
    --sky:#bcd3e6;
    --ink:#2a2a2a;
    --rule:#d7d7d7;
    --paper:#fbfbfa;
  }
  *{box-sizing:border-box;margin:0;padding:0}
  html,body{width:870px;height:1200px;overflow:hidden}
  body{background:var(--stage);font-family:"Cabin",sans-serif;color:var(--ink);position:relative}
  .spread{position:absolute;left:45px;width:780px;height:520px;display:flex;box-shadow:0 12px 28px rgba(0,0,0,.35)}
  .spread--outside{top:50px}
  .spread--inside{top:630px}
  .panel{position:relative;width:260px;height:100%;overflow:hidden;background:var(--paper)}
  .photo{position:absolute}

  /* Outside: intro panel */
  .intro{background:var(--orange-panel)}
  .intro .photo{left:0;top:0;width:260px;height:235px;background:linear-gradient(160deg,#5f8a3a 0%,#3d5d2a 40%,#c8372c 70%,#6f8e98 100%)}
  .intro-band{position:absolute;left:0;top:225px;width:260px;height:58px;background:var(--red);clip-path:polygon(0 0,100% 0,86% 100%,0 100%);padding:8px 0 0 44px}
  .intro-band h2{font-size:25px;font-weight:600;color:var(--orange);line-height:1}
  .intro-band p{font-size:12px;color:#fff;letter-spacing:.5px;margin:3px 0 0 48px}
  .intro-copy{position:absolute;left:44px;top:312px;width:190px;font-size:8.3px;line-height:1.55;color:#fff}
  .intro-copy p+p{margin-top:11px}

  /* Outside: offer list panel */
  .offers{padding:64px 42px 0 22px}
  .offers h3{font-size:14px;font-weight:400;color:var(--red);margin-bottom:6px}
  .checklist{list-style:none;margin-bottom:26px}
  .checklist li{display:flex;align-items:center;gap:8px;font-size:7.6px;height:16px;border-bottom:1px solid var(--rule)}
  .checklist li:last-child{border-bottom:none}
  .checklist svg{width:12px;height:11px;flex:none}
  .brand{display:flex;align-items:center;gap:5px;font-weight:700;color:var(--orange)}
  .brand i{display:block;border-radius:50%;background:var(--red)}
  .offers .brand{margin:10px 0 0 88px;font-size:15px}
  .offers .brand i{width:12px;height:12px}
  .contact{margin:10px 0 0 120px;font-size:6.3px;line-height:1.35;color:#666;font-style:normal}
  .contact dl{display:grid;grid-template-columns:24px 1fr;margin:8px 0 0 -24px;row-gap:1px}
  .contact dt{color:var(--red);font-weight:700;font-size:5.5px}
  .contact .web{margin-top:9px;padding-bottom:10px;border-bottom:1px solid var(--rule)}

  /* Outside: cover panel */
  .cover{background:linear-gradient(#fff 0,#eef1f4 160px)}
  .cover .brand{position:absolute;left:34px;top:58px;font-size:27px}
  .cover .brand i{width:18px;height:18px}
  .cover .photo{left:0;top:190px;width:260px;height:220px;background:linear-gradient(180deg,#7aa3c4 0%,#5c8a52 35%,#c62f2a 62%,#3f6d88 100%)}
  .cover-label{position:absolute;left:0;top:155px;width:200px;height:42px;background:#fff;clip-path:polygon(0 0,100% 0,93% 100%,0 100%);padding:5px 0 0 18px}
  .cover-label h1{font-size:17px;font-weight:600;color:var(--red);line-height:1.05}
  .cover-label p{font-size:8.5px;font-weight:600;color:var(--orange);letter-spacing:.3px}
  .cover-foot{position:absolute;left:0;top:395px;width:260px;height:125px;background:linear-gradient(rgba(43,106,140,0),var(--blue) 30px);padding:42px 0 0 42px}
  .cover-foot h2{font-size:14px;font-weight:500;color:var(--orange)}
  .cover-foot p{font-size:8.5px;color:#fff;line-height:1.35;margin-top:4px}

  /* Inside */
  .team-area{position:absolute;left:0;top:0;width:520px;height:520px;background:linear-gradient(var(--sky) 0,#d6e4ef 60%)}
  .team-band{position:absolute;left:0;top:44px;width:262px;height:54px;background:var(--orange);clip-path:polygon(0 0,100% 0,91% 100%,0 100%);padding:4px 0 0 40px}
  .team-band h2{font-size:23px;font-weight:500;color:var(--red)}
  .team-band p{font-size:9.5px;color:#fff;letter-spacing:.4px;margin-left:15px}
  .member{position:absolute;left:38px;display:flex;gap:7px;font-size:7.4px;line-height:1.5}
  .member--lead{top:130px}
  .member--org{top:216px;padding-top:10px;border-top:1px solid #9fb3c4;width:198px}
  .avatar{position:relative;width:58px;height:58px;border-radius:50%;flex:none;background:linear-gradient(140deg,#a58b5a,#5b6f3a)}
  .avatar b{position:absolute;left:-2px;bottom:6px;background:var(--red-tag);color:#fff;font-size:10px;font-weight:600;padding:1px 4px;letter-spacing:.4px}
  .member h4{font-size:7.2px;font-weight:500;color:var(--orange)}
  .bubble{position:absolute;border-radius:50%;border:2px solid #fff}
  .bubble--raft{left:272px;top:6px;width:200px;height:200px;background:linear-gradient(170deg,#7e8f71,#c8342b 55%,#5c6f70)}
  .bubble--crew{left:414px;top:108px;width:108px;height:108px;background:linear-gradient(150deg,#9ab0bd,#c63129 60%,#5d6a3b)}
  .bubble--meadow{left:280px;top:155px;width:132px;height:132px;background:linear-gradient(180deg,#b8cbd9 0%,#6c8a5a 40%,#77a13d 100%)}
  .river{left:0;top:300px;width:520px;height:220px;background:linear-gradient(180deg,rgba(214,228,239,0) 0%,#6f8d5a 20%,#9a5a44 45%,#5f7b53 70%,#4e5c4a 100%)}
  .archery{margin-left:520px}
  .archery .photo{left:0;top:0;width:260px;height:310px;background:linear-gradient(170deg,#a7b7a0 0%,#6f8a58 35%,#7f8583 65%,#c7c3bd 100%)}
  .archery .fade{position:absolute;left:0;top:250px;width:260px;height:60px;background:linear-gradient(rgba(251,251,250,0),var(--paper))}
  .more{position:absolute;left:27px;top:318px;width:192px}
  .more h2{font-size:14px;font-weight:400;color:var(--red);margin-bottom:12px}
  .more p{font-size:7.8px;line-height:1.65}
</style>
</head>
<body>
<svg width="0" height="0" style="position:absolute" aria-hidden="true">
  <symbol id="tick" viewBox="0 0 12 11"><path d="M1 6 L4.5 9.5 L11 1" fill="none" stroke="#e3891d" stroke-width="2.6" stroke-linecap="round" stroke-linejoin="round"/></symbol>
</svg>

<section class="spread spread--outside">
  <article class="panel intro">
    <div class="photo" role="img" aria-label="Foto: Jugendliche paddeln lachend in einem roten Kanu zwischen grünen Bäumen"></div>
    <div class="intro-band">
      <h2>Der Natur</h2>
      <p>EIN STÜCK NÄHER</p>
    </div>
    <div class="intro-copy">
      <p>Wir sind Ihr individueller Anbieter für Kanu-, Rad- und Erlebnistouren im Weser- und Leinebergland. Wir bieten Touren ab Hann.-Münden, Bad Karlshafen, Beverungen, Höxter, Holzminden, Polle, Bodenwerder, Hameln, Rinteln, Vlotho, Bad Oeynhausen, Porta Westfalica und Minden an.</p>
      <p>Mitten im Herzen Deutschlands organisieren wir Ihre Betriebs-, Gruppen-, und Schulklassenausfahrt zu fairen Preisen auf der Weser, Leine, Emmer, Diemel, Nethe, und Innerste. Auch Einzelreisende und Familien sind bei uns richtig, wenn es darum geht eine schöne Zeit draußen zu verbringen.</p>
    </div>
  </article>

  <article class="panel offers">
    <h3>Wir vermieten:</h3>
    <ul class="checklist">
      <li><svg><use href="#tick"/></svg>Kanus</li>
      <li><svg><use href="#tick"/></svg>Schlauchboote (Rafts)</li>
      <li><svg><use href="#tick"/></svg>SUP (Stand up Paddling)</li>
      <li><svg><use href="#tick"/></svg>Fahrräder</li>
    </ul>
    <h3>Wir organisieren:</h3>
    <ul class="checklist">
      <li><svg><use href="#tick"/></svg>Bogenschießen</li>
      <li><svg><use href="#tick"/></svg>Floßtouren</li>
      <li><svg><use href="#tick"/></svg>Nordic Walking</li>
      <li><svg><use href="#tick"/></svg>Abenteuer Großkanu</li>
      <li><svg><use href="#tick"/></svg>Tages- und Mehrtagestouren</li>
      <li><svg><use href="#tick"/></svg>Schulklassenausflüge</li>
    </ul>
    <div class="brand"><i></i>Flusszeit</div>
    <address class="contact">
      Flusszeit<br>Kanutouristik<br>Lena Kornfeld<br>37600 Talheim<br>(Am Fluss)
      <dl>
        <dt>TEL.</dt><dd>(0 51 20) 33 71 58</dd>
        <dt>MOBIL</dt><dd>(0 15 70) 44 26 913</dd>
      </dl>
      <dl class="web"><dt>WEB</dt><dd>www.flusszeit-touren.de</dd></dl>
    </address>
  </article>

  <article class="panel cover">
    <div class="brand"><i></i>Flusszeit</div>
    <div class="photo" role="img" aria-label="Foto: drei junge Frauen paddeln in einem roten Kanu vor einem alten Turm"></div>
    <div class="cover-label">
      <h1>Natur, Wasser, Spaß!</h1>
      <p>QUER DURCH HANNOVER</p>
    </div>
    <div class="cover-foot">
      <h2>Erlebnis auf dem Kanu</h2>
      <p>FÜR GRUPPEN WIE VEREINE,<br>SCHULKLASSEN UND FAMILIEN</p>
    </div>
  </article>
</section>

<section class="spread spread--inside">
  <div class="team-area">
    <div class="photo river" role="img" aria-label="Foto: zwei Paddler im roten Kanu vor einer alten Steinbogenbrücke"></div>
    <div class="team-band">
      <h2>Unser Team</h2>
      <p>ORGANISATION &amp; DURCHFÜHRUNG</p>
    </div>
    <div class="member member--lead">
      <div class="avatar" role="img" aria-label="Porträtfoto der Chefin im Kanu"><b>JULE</b></div>
      <div><h4>Chefin</h4>Durchführung aller Touren.<br>Am liebsten auf „wilden“ Gewässern<br>unterwegs.</div>
    </div>
    <div class="member member--org">
      <div class="avatar" role="img" aria-label="Porträtfoto des Organisators"><b>BENNO</b></div>
      <div><h4>Organisation und Kundenbetreuung</h4>Kanutouristiker (Paddelbund)<br>Kanu-Guide (Paddelbund)<br>Qualitätscoach Servicequalität<br>Gastland</div>
    </div>
    <div class="bubble bubble--raft" role="img" aria-label="Foto: Gruppe im Schlauchboot reckt die Paddel in die Luft"></div>
    <div class="bubble bubble--crew" role="img" aria-label="Foto: fröhliche Paddler in Schwimmwesten"></div>
    <div class="bubble bubble--meadow" role="img" aria-label="Foto: rote Kanus liegen auf einer Wiese am Ufer"></div>
  </div>
  <article class="panel archery">
    <div class="photo" role="img" aria-label="Foto: Frau beim Bogenschießen auf einer Wiese mit Zielscheibe"></div>
    <div class="fade"></div>
    <div class="more">
      <h2>Weitere Angebote</h2>
      <p>Wir bieten Ihnen das instinktive Bogenschießen als Baustein für Ihre Kanu-Tour, oder als Schnupperkurs an. Wann haben Sie sich in dieser hektischen Zeit zuletzt einmal nur auf Ihren Instinkt verlassen? In einer Welt, die voll ist mit technischen Finessen und immer bequemer werdenden Anwendungen ist uns der Bezug zum eigentlichen Leben fast gänzlich verloren gegangen. Wir wollen Ihnen zeigen, wie Sie sich wieder auf Ihren natürlichen Instinkt verlassen können. Weitere Informationen finden Sie auf unserer Website!</p>
    </div>
  </article>
</section>
</body>
</html>
```